Letter design, envelope design, and more

Hello, we the Tavrin Gmbh are looking for our shop. Letter C5. Design does not have to be like a business card, so it can have straight lines. Only the color is important. The logo is the text under TaVRin omit.It should not be playful but Profesionel

Font styles to use
Sans Serif

Colors
0555a3
3176b5
85abd2
85cae6
34a7d8
0792cd
cee9f5
cfdfed
000000

Requirements
Must have
• Color like business card, Please, with the text under TaVRin, Correct address Lindmattstr. 4 Zip code 9517 Seewil, as well as Couvert Without addressing only design and logo with TaVrn
Nice to have
• more writing articles
Should not have
• Not too colored, Text under TaVRin, bright colors

```html
<!DOCTYPE html>
<html lang="en">
<head>
<meta charset="utf-8">
<title>Tavrin Gmbh – Stationery</title>
<link href="https://fonts.googleapis.com/css2?family=Lato:ital,wght@0,400;0,700;1,700&family=Kaushan+Script&display=swap" rel="stylesheet">
<style>
  :root{
    --stage:#e1e2e4;
    --paper:#ffffff;
    --paper-shade:#ececee;
    --navy:#252a6b;
    --slate:#7f9db5;
    --ink:#3a3a40;
    --edge:#c9cacd;
    --ghost:#eceef3;
  }
  *{margin:0;padding:0;box-sizing:border-box}
  html,body{width:1200px;height:641px;overflow:hidden}
  body{background:var(--stage);font-family:"Lato",Arial,sans-serif;position:relative}

  /* Letterhead */
  .letter{position:absolute;left:66px;top:58px;width:364px;height:512px;
    background:linear-gradient(170deg,var(--paper) 35%,var(--paper-shade) 100%);
    border:1px solid var(--edge)}
  .letter__brand{position:absolute;top:22px;left:0;width:100%;text-align:center;
    font-weight:700;font-size:19px;letter-spacing:1px;color:var(--navy)}
  .letter__body{position:absolute;left:21px;top:86px;width:327px}
  .letter__salutation{font-weight:700;font-size:9.4px;color:var(--navy);margin-bottom:6px}
  .letter__body p{font-size:6.9px;line-height:11.2px;color:var(--ink);margin-bottom:8.5px}
  .letter__closing{position:absolute;left:21px;top:396px;font-size:11px;color:var(--ink)}
  .letter__signature{position:absolute;left:21px;top:411px;font-family:"Kaushan Script",cursive;
    font-size:16px;color:var(--navy)}
  .letter__footer{position:absolute;left:0;bottom:9px;width:100%;display:flex;justify-content:center;
    gap:6px;font-size:6.8px;color:var(--ink);align-items:center}
  .letter__footer span{display:flex;align-items:center;gap:3px}
  .letter__footer .sep{width:1px;height:8px;background:var(--edge)}
  .letter__footer svg{width:7px;height:7px}

  /* Envelopes */
  .envelope{position:absolute;background:var(--paper);border:1px solid var(--edge);overflow:hidden}
  .envelope--back{left:594px;top:84px;width:539px;height:242px}
  .envelope--open{left:554px;top:186px;width:540px;height:243px}
  .envelope--front{left:464px;top:294px;width:540px;height:243px}
  .envelope svg.flap{position:absolute;left:0;top:0}
  .envelope__brand{position:absolute;width:100%;text-align:center;font-weight:700;font-size:18px;letter-spacing:1px}
  .envelope--back .envelope__brand{top:31px;color:var(--paper)}
  .envelope--open .envelope__brand{top:37px;color:var(--navy)}

  .envelope__logo{position:absolute;left:16px;top:22px;font-weight:700;font-size:22px;letter-spacing:1px;color:var(--navy)}
  .envelope__address{position:absolute;left:16px;top:64px;font-size:9.6px;color:var(--ink);display:flex;align-items:center;gap:4px}
  .envelope__address svg{width:9px;height:9px}
  .envelope__web{position:absolute;left:16px;bottom:12px;font-size:9px;letter-spacing:2px;color:var(--ink)}
  .envelope__web em{font-style:normal;color:var(--slate)}
  .envelope__watermark{position:absolute;right:12px;bottom:-8px;font-weight:700;font-size:56px;color:var(--ghost);letter-spacing:1px}
</style>
</head>
<body>

<section class="letter">
  <div class="letter__brand">TAVRIN GMBH</div>
  <div class="letter__body">
    <div class="letter__salutation">Dear Mr. Lorem,</div>
    <p>Lorem ipsum dolor sit amet, consectetuer adipiscing elit, sed diam nonummy nibh euismod tincidunt ut laoreet dolore magna aliquam erat volutpat. Ut wisi enim ad minim veniam, quis nostrud exerci tation ullamcorper suscipit lobortis nisl ut aliquip ex ea commodo consequat. Duis autem vel eum iriure dolor in hendiusto odio dignissim qui blandit praesent luptatum zzril delenit.facilisi.</p>
    <p>Lorem ipsum dolor sit amet, consectetuer adipiscing elit, sed diam nonummy nibh euismod tincidunt ut laoreet dolore magna aliquam erat volutpat. Ut wisi enim ad minim veniam, quis nostrud exerci tation ullamcorper suscipit lobortis nisl ut aliquip ex ea commodo consequat.</p>
    <p>Lorem ipsum dolor sit amet, consectetuer adipiscing elit, sed diam nonummy nibh euismod tincidunt ut laoreet dolore magna aliquam erat volutpat. Ut wisi enim ad minim veniam, quis nostrud exerci tation ullamcorper suscipit lobortis nisl ut aliquip ex ea commodo consequat. Duis autem vel eum iriure dolor in hendiusto odio dignissim qui blandit praesent luptatum zzril delenit.facilisi.</p>
    <p>Lorem ipsum dolor sit amet, consectetuer adipiscing elit, sed diam nonummy nibh euismod tincidunt ut laoreet dolore magna aliquam erat volutpat. Ut wisi enim ad minim veniam, quis nostrud exerci tation ullamcorper suscipit lobortis nisl ut aliquip ex ea commodo consequat.</p>
    <p>Lorem ipsum dolor sit amet, consectetuer adipiscing elit, sed diam nonummy nibh euismod tincidunt ut laoreet dolore magna aliquam erat volutpat. Ut wisi enim ad minim veniam, quis nostrud exerci tation ullamcorper suscipit lobortis nisl ut aliquip ex ea commodo consequat. Duis autem vel eum iriure dolor in hendiusto odio dignissim qui blandit praesent luptatum zzril delenit.facilisi.</p>
    <p>Lorem ipsum dolor sit amet, consectetuer adipiscing elit, sed diam nonummy nibh euismod tincidunt ut laoreet dolore magna aliquam erat volutpat. Ut wisi enim ad minim veniam, quis nostrud exerci tation ullamcorper suscipit lobortis nisl ut aliquip ex ea commodo consequat.</p>
  </div>
  <div class="letter__closing">Sincerely Your,</div>
  <div class="letter__signature">Your Name</div>
  <div class="letter__footer">
    <span><svg viewBox="0 0 10 10"><circle cx="5" cy="5" r="4.3" fill="none" stroke="#252a6b" stroke-width="1"/><circle cx="5" cy="4.3" r="1.4" fill="#252a6b"/></svg>Lindmattstr. 4, Zip code 9517 Seewil</span>
    <i class="sep"></i>
    <span><svg viewBox="0 0 10 10"><circle cx="5" cy="5" r="4.3" fill="none" stroke="#252a6b" stroke-width="1"/><path d="M3.5 3l1 1-0.6 0.8c0.4 0.8 1 1.4 1.8 1.8L6.5 6l1 1-0.8 0.9C4.8 7.6 2.6 5.4 2.6 3.8z" fill="#252a6b"/></svg>+41 71 555 02 14</span>
    <i class="sep"></i>
    <span><svg viewBox="0 0 10 10"><rect x="1" y="2.5" width="8" height="5" fill="#252a6b"/><path d="M1 2.5l4 3 4-3" fill="none" stroke="#fff" stroke-width="0.8"/></svg>info@tavrin.ch</span>
    <i class="sep"></i>
    <span><svg viewBox="0 0 10 10"><circle cx="5" cy="5" r="4.2" fill="none" stroke="#252a6b" stroke-width="0.9"/><ellipse cx="5" cy="5" rx="1.8" ry="4.2" fill="none" stroke="#252a6b" stroke-width="0.7"/><path d="M1 5h8" stroke="#252a6b" stroke-width="0.7"/></svg>www.tavrin.ch</span>
  </div>
</section>

<section class="envelope envelope--back">
  <svg class="flap" width="539" height="100" viewBox="0 0 539 100">
    <path d="M0 0H539L531 30Q525 55 490 60L300 92Q270 97 240 92L50 60Q14 55 8 30Z" fill="#7f9db5"/>
  </svg>
  <div class="envelope__brand">TAVRIN</div>
</section>

<section class="envelope envelope--open">
  <svg class="flap" width="540" height="100" viewBox="0 0 540 100">
    <path d="M0 0Q8 40 40 48L250 94Q270 98 290 94L500 48Q532 40 540 0" fill="none" stroke="#c9cacd" stroke-width="1"/>
  </svg>
  <div class="envelope__brand">TAVRIN</div>
</section>

<section class="envelope envelope--front">
  <div class="envelope__watermark">TAVRIN</div>
  <div class="envelope__logo">TAVRIN GMBH</div>
  <div class="envelope__address">
    <svg viewBox="0 0 10 10"><circle cx="5" cy="5" r="4.3" fill="none" stroke="#252a6b" stroke-width="1"/><circle cx="5" cy="4.3" r="1.4" fill="#252a6b"/></svg>
    Lindmattstr. 4, Zip code 9517 Seewil
  </div>
  <div class="envelope__web">www.<em>tavrin</em>.ch</div>
</section>

</body>
</html>
```